Either a trifold or double sided flyer/brochure

A flyer to help spark interest in a historic preservation project in Ashbrook, NH--looking for something that captures the early 19th century rural village and mill times--American Primitive, Shaker, Cross Stitch Sampler...must be able to highlight home history as well as have all owners of house on a single page. Word document attached--can also provide files for the house painting, color photos, borrell photo, advertising photo or part of original settler map.
I like this brochure
http://tessavornick.com/wordpress/dell-lodge-museum-brochure/
community stakeholders, residents,
Historic Preservation, House Museums.

```html
<!DOCTYPE html>
<html lang="en">
<head>
<meta charset="utf-8">
<title>Halloway Homestead Flyer</title>
<link href="https://fonts.googleapis.com/css2?family=Oswald:wght@500&family=Libre+Baskerville:wght@400&family=Cinzel:wght@400&display=swap" rel="stylesheet">
<style>
:root{
  --canvas:#ececec;
  --paper-light:#efe3c8;
  --paper-mid:#e2d1ad;
  --paper-edge:#c9ae80;
  --ink:#3a2a1b;
  --ink-soft:#4d3b2a;
  --band-dark:#2a1a0e;
  --brown:#6b4a30;
  --brown-dark:#4e3420;
  --cream:#f3e8d2;
  --sepia-a:#8a6d47;
  --sepia-b:#5e4429;
  --sepia-c:#b59a70;
  --tear:#f7f3ea;
}
*{box-sizing:border-box;margin:0;padding:0}
html,body{width:783px;height:1200px;overflow:hidden;background:var(--canvas)}
.sheet-stack{position:relative;width:783px;height:1200px}
.page-slot{position:absolute;left:186px;width:410px;height:580px}
.page-slot.front{top:12px}
.page-slot.back{top:608px}
.page{
  position:absolute;left:0;top:0;width:676px;height:955px;
  transform:scale(0.6065);transform-origin:top left;
  background:radial-gradient(ellipse at 50% 55%,var(--paper-light) 0%,var(--paper-mid) 70%,var(--paper-edge) 100%);
  box-shadow:0 3px 10px rgba(0,0,0,.25);overflow:hidden;
  font-family:"Libre Baskerville",Georgia,serif;color:var(--ink);
}
.photo{position:absolute}
.photo.sepia-warm{background:linear-gradient(160deg,var(--sepia-c),var(--sepia-a) 55%,var(--sepia-b))}
.photo.sepia-light{background:linear-gradient(170deg,#d8c39c,#a98a5e 60%,#7d6240)}
.photo.sepia-dark{background:linear-gradient(165deg,#7a5f3e,#4a3520 70%,#33230f)}
.torn-edge{position:absolute;left:0;width:676px}
.page-footer{position:absolute;left:47px;right:42px;top:912px;display:flex;align-items:center;gap:10px;font-size:11px;font-weight:700;color:var(--ink)}
.page-footer .rule{flex:1;height:1px;background:var(--ink-soft)}
.page-base{position:absolute;left:0;bottom:0;width:676px;height:11px;background:var(--brown-dark)}

/* front */
.history-title{position:absolute;left:47px;top:336px;font-family:"Oswald","Arial Narrow",sans-serif;font-weight:500;font-size:21px;line-height:32px;color:var(--ink);text-transform:uppercase;letter-spacing:-.2px}
.body-copy{font-size:7.6px;line-height:11.8px;color:var(--ink-soft);text-align:justify}
.body-copy p{margin-bottom:9px}
.column-copy{position:absolute;left:47px;top:414px;width:332px}
.wide-copy{position:absolute;left:47px;top:697px;width:588px}

/* back */
.title-band{position:absolute;left:0;top:0;width:676px;height:100px;background:var(--band-dark);color:var(--cream);text-align:center;font-size:19px;line-height:27px;padding-top:18px}
.owners-tab{position:absolute;left:150px;top:310px;width:380px;height:88px;background:var(--brown);border-radius:0 0 12px 12px;color:var(--cream);font-family:"Cinzel",Georgia,serif;font-size:17.5px;line-height:23px;text-align:center;padding-top:33px;letter-spacing:.5px}
.owner-list{position:absolute;left:32px;top:424px;width:372px;list-style:none;font-size:9.2px;line-height:12px;color:var(--ink)}
.owner-list li{display:flex;justify-content:space-between;align-items:flex-end;margin-bottom:15px}
.owner-list li.two-line{margin-bottom:15px}
.owner-list .years{white-space:nowrap;padding-left:10px}
.ad-box{position:absolute;left:32px;top:760px;width:370px;height:136px;background:var(--brown);border-radius:8px;color:var(--cream);overflow:hidden}
.ad-name{position:absolute;left:22px;top:16px;font-family:"Cinzel",Georgia,serif;font-size:17px;letter-spacing:.5px}
.ad-trade{position:absolute;left:192px;top:0;width:178px;height:40px;background:var(--brown-dark);font-size:12px;line-height:10px;padding:13px 0 0 16px;border-bottom-left-radius:6px}
.ad-divider{position:absolute;left:0;right:0;top:46px;border-top:1px dashed rgba(243,232,210,.7)}
.ad-vdivider{position:absolute;left:196px;top:58px;height:58px;border-left:1px dashed rgba(243,232,210,.7)}
.ad-col{position:absolute;top:60px}
.ad-col h3{font-family:"Cinzel",Georgia,serif;font-weight:400;font-size:13.5px;letter-spacing:.6px;margin-bottom:4px}
.ad-col p{font-size:7.6px;line-height:10px}
.ad-col.left{left:22px;width:165px}
.ad-col.right{left:210px;width:150px}
</style>
</head>
<body>
<main class="sheet-stack">

  <!-- Front side: homestead history -->
  <div class="page-slot front">
    <article class="page">
      <div class="photo sepia-warm" style="left:0;top:0;width:426px;height:320px" role="img" aria-label="Sepia photo of the homestead and barn among tall trees"></div>
      <div class="photo sepia-light" style="left:434px;top:0;width:242px;height:320px" role="img" aria-label="Sepia photo of the clapboard gable end with tree shadows"></div>
      <svg class="torn-edge" style="top:286px" width="676" height="44" viewBox="0 0 676 44" aria-hidden="true">
        <path d="M0 14 L28 18 L55 12 L80 20 L110 15 L140 22 L170 13 L200 19 L228 14 L255 21 L290 16 L318 11 L350 18 L380 13 L410 20 L440 10 L468 16 L500 12 L530 19 L560 14 L590 20 L620 12 L648 17 L676 13 L676 44 L0 44 Z" fill="rgba(0,0,0,.18)"/>
        <path d="M0 18 L28 22 L55 16 L80 25 L110 19 L140 26 L170 17 L200 24 L228 18 L255 26 L290 20 L318 15 L350 23 L380 17 L410 25 L440 14 L468 21 L500 16 L530 24 L560 18 L590 25 L620 16 L648 22 L676 17 L676 31 L648 34 L620 29 L590 35 L560 30 L530 36 L500 31 L468 37 L440 30 L410 36 L380 31 L350 37 L318 30 L290 35 L255 32 L228 37 L200 31 L170 36 L140 32 L110 37 L80 31 L55 36 L28 31 L0 35 Z" fill="var(--tear)"/>
        <path d="M0 35 L28 31 L55 36 L80 31 L110 37 L140 32 L170 36 L200 31 L228 37 L255 32 L290 35 L318 30 L350 37 L380 31 L410 36 L440 30 L468 37 L500 31 L530 36 L560 30 L590 35 L620 29 L648 34 L676 31 L676 44 L0 44 Z" fill="var(--paper-mid)"/>
      </svg>

      <h1 class="history-title">The Halloway Homestead History c. 1826<br>Ashbrook, New Hampshire</h1>

      <div class="photo sepia-dark" style="left:413px;top:348px;width:226px;height:208px" role="img" aria-label="Aged portrait photo of a woman in a dark dress standing before the house"></div>
      <div class="photo sepia-light" style="left:413px;top:568px;width:226px;height:106px" role="img" aria-label="Painting of the homestead in a snowy winter landscape"></div>

      <div class="column-copy body-copy">
        <p>In 1826, George S. Halloway and his wife, Jane (Ames) Halloway purchased 26 acres from Robert Faye on the Quillan River, north of Pratt's Woolen Mill in South Ashbrook, NH. This parcel was carved out lot #32 which was comprised of 268 acres that were deeded to John Faye (Robert Faye's grandfather) by Jeremiah Stockard and John Merritt on May 5, 1762. It is believed that Halloway, who was blacksmith, built the house that currently stands at 47 Alder Street in Ashbrook, NH. He also built his forge on the site down by the river. It is likely that much of the forged hardware in the home was crafted by him. Feeling the need to leave Ashbrook for a new frontier, Halloway left town with his brother, Bradley, to purchase land in the emerging communities of Orleans County, NY. Before doing so, Halloway sold the home, shop and buildings to Thomas Garner and his wife Alice (Hollis) Garner in 1828.</p>
        <p>By trade, Thomas Garner was a cloth dresser and wool-carder. He was also a deeply religious man and served as deacon in the emerging, but still quite small, Baptist community. In those days, small groups of the Baptists and Methodists met in the Wendell Home for bible study, prayers and singing. The Wendells were well known abolitionists and their house served as a stop on the Underground Railroad. Deacon Garner died in 1839 and his estate was managed by Samuel Hollis—very likely a relative of Alice—who protected Alice's dower. The property was then sold to Elijah Brown Ashby and his wife Achsah (Crane) Ashby.</p>
      </div>

      <div class="wide-copy body-copy">
        <p>Elijah was quite industrious and continued to expand the wool mill. He was an early investor in the Keswick Railroad and ceded a right of way to the railroad on the homestead. The mill eventually came under the control of his son, Henry A. Ashby, and operated until it burned down on April 20, 1874. Elijah passed away in 1877 and left the home to Mary Ellen Ashby who was most commonly known as "Ellen."</p>
        <p>Ellen Ashby was approached in 1891 by Allie Pratt, the owner of the Pratt's Mill Complex, to ask if she would be willing to rent out the home to a couple from Boston. This turned out to be Marian and Edward Larkin, the founders of the Larkin Colony, who ended up spending their first summer in Ashbrook, NH in the home. Marian recalls in her writings: "You can't fail to remember the two-story farmhouse almost across from the road from the iron bridge, now occupied by the Borrell Family. It had never been painted and was a lovely soft gray in color. There were really only four rooms and a kitchen, spotlessly clean and adequately furnished, which really didn't mean much but some chairs, tables and beds. Then in the kitchen was something that fascinated me, a stone bowl into which the clearest of water was all the time pouring and then running off into a drain...."</p>
        <p>The Borrells lived in this home for the longest time of any owner—and some refer to this area before the bridge, as Borrells Corner. This moment of stewardship began under Fred Parker Borrell and his wife Grace E. (Dorsey) Borrell around 1904 and lasted until 2015 when a descendant sold the home. The house is now under the stewardship of Edward M. Solano and Albert A. Whitcomb, Jr. and will be undergoing a significant restoration.</p>
      </div>

      <footer class="page-footer"><span>www.yourwebsite.com</span><span class="rule"></span></footer>
      <div class="page-base"></div>
    </article>
  </div>

  <!-- Back side: owners -->
  <div class="page-slot back">
    <article class="page">
      <header class="title-band">Halloway Homestead c. 1826, Borrells Corner,<br>Ashbrook, New Hampshire</header>

      <div class="photo sepia-light" style="left:0;top:96px;width:186px;height:222px" role="img" aria-label="Sepia photo of the interior staircase and newel post"></div>
      <div class="photo sepia-dark" style="left:192px;top:96px;width:188px;height:222px" role="img" aria-label="Sepia close-up of a forged iron door handle on a weathered door"></div>
      <div class="photo sepia-warm" style="left:388px;top:96px;width:288px;height:222px" role="img" aria-label="Folk painting of the white homestead and barn"></div>
      <svg class="torn-edge" style="top:86px" width="676" height="20" viewBox="0 0 676 20" aria-hidden="true">
        <path d="M0 0 L676 0 L676 12 L650 15 L620 9 L590 14 L560 8 L530 13 L500 10 L470 16 L440 9 L410 14 L380 8 L350 13 L320 9 L290 15 L260 10 L230 14 L200 8 L170 13 L140 9 L110 15 L80 10 L50 14 L20 9 L0 13 Z" fill="var(--band-dark)"/>
      </svg>
      <svg class="torn-edge" style="top:296px" width="676" height="40" viewBox="0 0 676 40" aria-hidden="true">
        <path d="M0 14 L30 19 L60 12 L92 20 L120 14 L152 21 L185 13 L215 18 L245 12 L275 20 L305 14 L338 22 L370 13 L400 19 L430 12 L462 20 L495 14 L525 21 L555 13 L590 19 L620 12 L650 18 L676 13 L676 28 L650 32 L620 27 L590 33 L555 28 L525 33 L495 29 L462 34 L430 28 L400 33 L370 28 L338 34 L305 29 L275 33 L245 28 L215 34 L185 29 L152 34 L120 29 L92 33 L60 28 L30 33 L0 29 Z" fill="var(--tear)"/>
        <path d="M0 29 L30 33 L60 28 L92 33 L120 29 L152 34 L185 29 L215 34 L245 28 L275 33 L305 29 L338 34 L370 28 L400 33 L430 28 L462 34 L495 29 L525 33 L555 28 L590 33 L620 27 L650 32 L676 28 L676 40 L0 40 Z" fill="var(--paper-mid)"/>
      </svg>

      <h2 class="owners-tab">Owners of 47 Alder Street<br>Ashbrook, New Hampshire</h2>

      <ul class="owner-list">
        <li><span>Robert Faye (grandson of John Faye) owned the land</span><span class="years">1826</span></li>
        <li><span>George S. Halloway and Jane (Ames) Halloway</span><span class="years">1826–1828</span></li>
        <li><span>Deacon Thomas Garner and Alice (Hollis) Garner (Baptist)</span><span class="years">1828–1839</span></li>
        <li class="two-line"><span>Elijah Brown Ashby and Achsah (Crane) Ashby<br>(mortgage between Samuel Hollis and Ashby is 1845)</span><span class="years">1839–1877</span></li>
        <li><span>Mary Ellen Ashby</span><span class="years">1877–1898</span></li>
        <li><span>James Corliss</span><span class="years">1898–1904</span></li>
        <li><span>Fred Parker Borrell and Grace E. (Dorsey) Borrell</span><span class="years">1904–1956</span></li>
        <li class="two-line"><span>Elinor (Borrell) Tennant and Frank O Tennant<br>(Elinor was born in house on July 29, 1911)</span><span class="years">1955–1998</span></li>
        <li class="two-line"><span>James H. Vandermeer and Maria Ruiz Vandermeer<br>(James was nephew of Elinor (Borrell) Tennant)</span><span class="years">1998–2015</span></li>
        <li><span>Riverglen</span><span class="years">2015–2022</span></li>
        <li><span>Edward M. Solano and Albert A. Whitcomb, Jr.</span><span class="years">2022</span></li>
      </ul>

      <div class="photo" style="left:432px;top:422px;width:218px;height:190px;background:linear-gradient(160deg,#dcd6c6,#c4bca8 60%,#a89e86)" role="img" aria-label="Section of the early settler lot map showing lots 32 to 36 along the river"></div>
      <div class="photo sepia-dark" style="left:432px;top:628px;width:218px;height:268px" role="img" aria-label="Aged photo of an elderly couple seated at home before flowers"></div>

      <section class="ad-box" aria-label="1878 trade advertisement">
        <div class="ad-name">H. A. Ashby,</div>
        <div class="ad-trade">Wool Carder, Cloth<br>Dresser</div>
        <div class="ad-divider"></div>
        <div class="ad-vdivider"></div>
        <div class="ad-col left">
          <h3>AND WOOL DYER</h3>
          <p>Garments of all kinds re-dyed.<br>Dyes prepared for family use, with directions for coloring.</p>
        </div>
        <div class="ad-col right">
          <h3>ALDER STREET</h3>
          <p>Ashbrook', N.H., May 7, 1878</p>
        </div>
      </section>

      <footer class="page-footer"><span>www.yourwebsite.com</span><span class="rule"></span></footer>
      <div class="page-base"></div>
    </article>
  </div>

</main>
</body>
</html>
```